Commercial Real Estate

We need a business card design for a new commercial real estate business that specializes in apartment building brokerage. Not individual units but the entire complex. We find and represent the owners existing buildings and well as new buyers for those buildings. The design should convey trust, integrity, knowledge and growth. It should be easily read.

Target Market(s)

40 to 65 years old

Industry/Entity Type

Real Estate

```html
<!DOCTYPE html>
<html lang="en">
<head>
<meta charset="utf-8">
<title>Keystead Property Investments – Business Card</title>
<link rel="stylesheet" href="https://fonts.googleapis.com/css2?family=Ubuntu:wght@300;500;700&family=Roboto+Condensed:wght@400&display=swap">
<style>
  :root {
    --teal: #55b8bb;
    --slate: #465a5c;
    --ink: #1f1d1d;
    --paper: #ffffff;
    --paper-shade: #f3f5f5;
  }
  html, body {
    margin: 0;
    padding: 0;
    overflow: hidden;
    background: var(--paper);
  }
  .card {
    position: relative;
    width: 1200px;
    height: 725px;
    overflow: hidden;
    background: linear-gradient(135deg, var(--paper-shade) 0%, var(--paper) 45%, var(--paper) 100%);
    font-family: "Ubuntu", sans-serif;
  }
  .card__waves {
    position: absolute;
    inset: 0;
    width: 1200px;
    height: 725px;
  }
  .wave--teal { fill: var(--teal); }
  .wave--slate { fill: var(--slate); }
  .wave--paper { fill: var(--paper); }

  .holder {
    position: absolute;
    right: 75px;
    top: 72px;
    text-align: right;
    color: var(--ink);
  }
  .holder__name {
    margin: 0;
    font-weight: 700;
    font-size: 43px;
    line-height: 1.1;
  }
  .holder__role {
    margin: 6px 0 0;
    font-weight: 300;
    font-size: 27px;
    line-height: 1.1;
  }

  .brand {
    position: absolute;
    left: 118px;
    top: 462px;
    display: flex;
    align-items: center;
    gap: 16px;
    color: var(--slate);
  }
  .brand__mark {
    width: 22px;
    height: 22px;
    background: var(--teal);
    flex: none;
  }
  .brand__name {
    margin: 0;
    font-weight: 500;
    font-size: 30px;
    line-height: 1.2;
    letter-spacing: 1px;
  }

  .contacts {
    position: absolute;
    right: 50px;
    top: 468px;
    margin: 0;
    padding: 0;
    list-style: none;
    font-family: "Roboto Condensed", sans-serif;
    font-size: 27px;
    color: var(--ink);
  }
  .contacts__item {
    display: flex;
    justify-content: flex-end;
    align-items: flex-start;
    gap: 22px;
    height: 44px;
    text-align: right;
    line-height: 40px;
  }
  .contacts__item--address {
    line-height: 44px;
    height: auto;
  }
  .contacts__icon {
    width: 30px;
    height: 30px;
    margin-top: 6px;
    flex: none;
    fill: var(--ink);
  }
</style>
</head>
<body>
<main class="card">
  <svg class="card__waves" viewBox="0 0 1075 649" preserveAspectRatio="none" aria-hidden="true">
    <path class="wave--teal" d="M0 560 C 160 640 380 650 580 570 C 760 495 880 360 1075 318 L1075 649 L0 649 Z"/>
    <path class="wave--paper" d="M0 540 C 160 610 360 620 520 590 C 420 640 200 640 0 590 Z"/>
    <path class="wave--slate" d="M0 502 C 130 575 330 610 500 590 C 560 582 610 565 650 548 C 600 585 500 615 400 620 C 240 628 100 600 0 560 Z"/>
    <path class="wave--slate" d="M95 538 C 300 585 500 565 700 455 C 850 372 950 318 1075 306 L1075 322 C 960 334 860 388 720 468 C 520 580 310 592 95 538 Z"/>
  </svg>

  <header class="holder">
    <h1 class="holder__name">Your Name</h1>
    <p class="holder__role">owner</p>
  </header>

  <div class="brand">
    <span class="brand__mark"></span>
    <p class="brand__name">Keystead<br>Property Investments</p>
  </div>

  <ul class="contacts">
    <li class="contacts__item">
      <span>00000000000</span>
      <svg class="contacts__icon" viewBox="0 0 24 24" aria-hidden="true"><path d="M3 9c0-3 4-5 9-5s9 2 9 5v2h-5V9.5c-1-.5-2.5-.8-4-.8s-3 .3-4 .8V11H3z"/><path d="M6 12h12l2 8H4z"/></svg>
    </li>
    <li class="contacts__item">
      <span>www.website.com</span>
      <svg class="contacts__icon" viewBox="0 0 24 24" aria-hidden="true"><path d="M12 2a10 10 0 1 0 0 20 10 10 0 0 0 0-20zm6.9 6h-3a15 15 0 0 0-1.3-4A8 8 0 0 1 18.9 8zM12 4c.8 1.1 1.5 2.5 1.9 4h-3.8c.4-1.5 1.1-2.9 1.9-4zM4.3 14a8 8 0 0 1 0-4h3.3a16 16 0 0 0 0 4zm.8 2h3a15 15 0 0 0 1.3 4A8 8 0 0 1 5.1 16zm3-8h-3a8 8 0 0 1 4.3-4A15 15 0 0 0 8.1 8zM12 20c-.8-1.1-1.5-2.5-1.9-4h3.8c-.4 1.5-1.1 2.9-1.9 4zm2.3-6H9.7a14 14 0 0 1 0-4h4.6a14 14 0 0 1 0 4zm.3 6a15 15 0 0 0 1.3-4h3a8 8 0 0 1-4.3 4zm1.8-6a16 16 0 0 0 0-4h3.3a8 8 0 0 1 0 4z"/></svg>
    </li>
    <li class="contacts__item">
      <span>yourname@website.com</span>
      <svg class="contacts__icon" viewBox="0 0 24 24" aria-hidden="true"><path d="M2 5h20v14H2zm2.5 2 7.5 6 7.5-6zm-.5 1.8V17h16V8.8l-8 6.4z"/></svg>
    </li>
    <li class="contacts__item contacts__item--address">
      <span>Your commercial address in<br>just two line</span>
      <svg class="contacts__icon" viewBox="0 0 24 24" aria-hidden="true"><path d="M12 1a7 7 0 0 0-7 7c0 5 7 15 7 15s7-10 7-15a7 7 0 0 0-7-7zm0 10a3 3 0 1 1 0-6 3 3 0 0 1 0 6z"/></svg>
    </li>
  </ul>
</main>
</body>
</html>
```